We need a Welcome Booklet designed for our Church - Harrowgate Fields Church. We would like a design that is contemporary with no religious symbols or old pictures. Please use quality contemporary photos . See attached a Word document with what content we want in the booklet.

Target Market(s)

Guests to the church so new person friendly

Requirements
Must have
• A contemporary modern look
Should not have
• Religious symbols or old pictures

```html
<!DOCTYPE html>
<html lang="en">
<head>
<meta charset="utf-8">
<title>Sunday celebration – Harrowgate Fields Church</title>
<link rel="stylesheet" href="https://fonts.googleapis.com/css2?family=Bitter:wght@400&family=Jost:wght@400;600&display=swap">
<style>
  :root {
    --ink: #1b1b1b;
    --orange: #f7941d;
    --link-red: #e8141b;
    --header-deep: #06162c;
    --header-mid: #123a6b;
    --header-light: #2a64a8;
    --paper: #ffffff;
  }
  * { margin: 0; padding: 0; box-sizing: border-box; }
  html, body { width: 855px; height: 1200px; overflow: hidden; background: var(--paper); }
  .page {
    position: relative; width: 855px; height: 1200px;
    font-family: "Jost", "Century Gothic", sans-serif;
    color: var(--ink);
  }
  .hero {
    position: absolute; left: 0; top: 0; width: 855px; height: 199px;
    background:
      radial-gradient(ellipse 260px 160px at 720px 60px, rgba(80,140,210,.55), transparent 70%),
      radial-gradient(ellipse 200px 120px at 430px 70px, rgba(60,110,180,.45), transparent 70%),
      linear-gradient(180deg, var(--header-mid) 0%, var(--header-deep) 100%);
  }
  .hero-title {
    position: absolute; left: 55px; top: 118px;
    font-family: "Bitter", Georgia, serif; font-weight: 400;
    font-size: 47px; line-height: 56px; color: #fff; letter-spacing: -0.3px;
  }
  .intro { position: absolute; left: 68px; top: 224px; width: 740px; }
  .intro-heading { font-weight: 600; font-size: 24px; line-height: 30px; }
  .service-times { margin-top: 8px; color: var(--orange); font-weight: 600; font-size: 24.5px; line-height: 39px; }
  .intro-text { margin-top: 14px; font-size: 21.5px; line-height: 28px; }
  .pillars { list-style: none; margin-top: 16px; color: var(--orange); font-size: 21.5px; line-height: 28.5px; }
  .ministry { position: absolute; width: 760px; font-size: 20.5px; line-height: 28px; }
  .ministry h2 { font-size: 19.5px; font-weight: 600; line-height: 28px; }
  .ministry .link { color: var(--link-red); font-weight: 600; }
  .children { left: 68px; top: 546px; }
  .youth { left: 68px; top: 680px; }
  .students { left: 71px; top: 837px; }
  .lounge { left: 71px; top: 973px; }
</style>
</head>
<body>
<main class="page">
  <header class="hero" role="img" aria-label="Photo of a worship band singing on a stage under blue lighting">
    <h1 class="hero-title">Sunday celebration</h1>
  </header>

  <section class="intro">
    <p class="intro-heading">Worship with us on Sunday</p>
    <p class="service-times">First Service: - 9:00 AM - 10:30 AM<br>Second Service: - 11:15 AM -12:45 PM</p>
    <p class="intro-text">Our Sunday celebration services are designed to help people<br>experience the grace and love of God through:</p>
    <ul class="pillars">
      <li>Worship</li>
      <li>Biblical teaching</li>
      <li>A loving community</li>
    </ul>
  </section>

  <section class="ministry children">
    <h2>CHILDREN (0-11 years)</h2>
    <p>HFCKids is a vibrant ministry where the children have their own fun<br>filled lessons and activities. There is also a crèche for toddlers and a<br>separate Mother's and Babies room.<br>For more information on HFCKids please visit <span class="link">hfc.church/children</span></p>
  </section>

  <section class="ministry youth">
    <h2>YOUNG PEOPLE (11-17 years)</h2>
    <p>FieldsYouth is a buzzing ministry for our young people to explore, grow<br>and thrive with an excellent young leaders programme.<br>For more information on FieldsYouth, please visit <span class="link">hfc.church/youth</span></p>
  </section>

  <section class="ministry students">
    <h2>20 &amp; STUDENTS</h2>
    <p>AsOne is a community of young adult who build relationships and<br>mission that are truly transformative. For more information on<br>AsOne, please visit <span class="link">hfc.church/students</span></p>
  </section>

  <section class="ministry lounge">
    <h2>GUEST LOUNGE</h2>
    <p>Don’t rush home, please stop by at our Guest Lounge in the Meadow<br>Café, we would love to you to connect with you further.<br>Refreshments are available after both services.</p>
  </section>
</main>
</body>
</html>
```